Catering Menu Package

I currently have a complete menu package, which we have redesigned as far as content, now I need to it put together in a catalog type format. It is essentially 10-12 pages in length, and will be sent for print production. Upon receiving a final edit
Updates

I have added an example gif to the project.

I did this free hand this basically what I am looking for. please change text and type to whatever you think would look best. This is a total rough design so, feel free to change any and everything. The text for the page is on the word documents. If you need more images let me know I am in the process of getting as many images uploaded for your use.

Project Deadline Extended
Reason: I figured we got a late jump with questions, so i am extending a few days .

Target Market(s)

The target market is business who wish to have catered luncheons, breakfasts , meetings

Industry/Entity Type

Catering

Requirements
Must have
• I have attached a copy of the text that what we want in the package, our logo, and i have also attached a catering package of another company to give you an idea what the finished product will be
Should not have
• It should not look identical to the example catering packages, these are for some inspiration we want our own design with the same type of look and feel

```html
<!DOCTYPE html>
<html lang="en">
<head>
<meta charset="utf-8">
<title>Harbor Field Caterers – Menu Pages 7 &amp; 8</title>
<link rel="stylesheet" href="https://fonts.googleapis.com/css2?family=Alegreya:ital,wght@0,400;0,700;1,400;1,700&family=Lobster+Two:ital,wght@1,700&display=swap">
<style>
:root{
  --backdrop:#6b4a2e;
  --paper:#ebe4d8;
  --orange:#f07a2a;
  --orange-text:#ef7b2f;
  --green:#6ab04c;
  --ink:#161616;
  --white:#ffffff;
  --cookie-dark:#7a4e2a;
  --cookie-light:#e6c79a;
  --plate-light:#f3efe6;
  --chicken:#c9a25e;
}
*{box-sizing:border-box;margin:0;padding:0}
html,body{width:1200px;height:800px;overflow:hidden;background:var(--backdrop)}
.canvas{position:relative;width:1200px;height:800px}
.page{position:absolute;top:18px;width:568px;height:744px;background:var(--paper);overflow:hidden;font-family:"Alegreya",serif;color:var(--ink)}
.page--front{left:20px}
.page--back{left:606px}
.abs{position:absolute}
.photo{position:absolute;left:0;top:0;width:568px;height:744px}
.section-rule{position:absolute;left:0;width:440px;height:3px;background:var(--orange)}
.section-title{position:absolute;height:38px;background:var(--orange);color:var(--white);font-family:"Lobster Two",cursive;font-style:italic;font-weight:700;font-size:27px;line-height:38px;text-align:center}
.combo-name{position:absolute;left:28px;font-style:italic;font-size:24px;color:var(--orange-text);white-space:nowrap;letter-spacing:.3px}
.combo-price{position:absolute;left:337px;font-weight:700;font-size:25px;letter-spacing:1px}
.addon-name{position:absolute;font-style:italic;font-weight:700;font-size:14px;color:var(--orange-text);line-height:20px;white-space:nowrap}
.addon-price{position:absolute;font-weight:700;font-size:15px;line-height:20px}
.entree-name{position:absolute;left:24px;font-style:italic;font-weight:700;font-size:17px;color:var(--orange-text);line-height:17px;white-space:nowrap}
.entree-desc{position:absolute;left:24px;width:440px;font-size:12.4px;line-height:18px}
.entree-price{position:absolute;left:331px;font-weight:700;font-size:18px;line-height:20px;letter-spacing:.5px}
.notice{position:absolute;top:655px;height:28px;border-radius:8px;background:var(--green);color:var(--white);font-size:10px;line-height:12px;text-align:center;padding-top:2px}
.footer{position:absolute;left:0;top:686px;width:432px;height:58px;background:var(--orange);color:var(--white)}
.footer__cta{position:absolute;left:21px;top:5px;font-style:italic;font-size:10px}
.footer__phone{position:absolute;left:16px;top:20px;display:flex;align-items:center;gap:6px;font-style:italic;font-weight:700;font-size:21px}
.footer__address{position:absolute;left:242px;top:6px;font-size:10px;line-height:13px}
.brand{position:absolute;left:432px;top:517px;width:136px;height:227px;background:var(--white);display:flex;flex-direction:column;align-items:center;justify-content:center;gap:14px}
.brand__dot{width:46px;height:46px;border-radius:50%;background:var(--orange)}
.brand__name{font-size:19px;line-height:22px;text-align:center;color:var(--ink)}
</style>
</head>
<body>
<main class="canvas">

  <!-- Page 7 -->
  <section class="page page--front">
    <svg class="photo" viewBox="0 0 568 744" role="img" aria-label="Photo of fresh baked chocolate chip cookies">
      <defs>
        <linearGradient id="cookieTone" x1="0" y1="0" x2="0" y2="1">
          <stop offset="0" stop-color="#efe6d6"/>
          <stop offset=".35" stop-color="var(--cookie-light)"/>
          <stop offset=".75" stop-color="#b9814a"/>
          <stop offset="1" stop-color="var(--cookie-dark)"/>
        </linearGradient>
      </defs>
      <path d="M472 0 C440 160 520 330 428 517 L568 517 L568 0 Z" fill="url(#cookieTone)"/>
    </svg>

    <div class="section-rule" style="top:27px"></div>
    <h2 class="section-title" style="left:87px;top:12px;width:266px">Sandwhich Combos</h2>

    <p class="combo-name" style="top:66px">One Side with any Sandwhich</p>
    <p class="combo-price" style="top:90px">$&amp;.&amp;&amp;&amp;</p>
    <p class="combo-name" style="top:129px">Two Sides with and Snadwhich</p>
    <p class="combo-price" style="top:152px">$&amp;.&amp;&amp;&amp;</p>
    <p class="combo-name" style="top:196px">Gorumet</p>
    <p class="combo-price" style="top:196px">$&amp;.&amp;&amp;</p>
    <p class="combo-name" style="top:241px">Two Sides and A Fresh Baked Cookie</p>
    <p class="combo-price" style="top:265px">$&amp;.&amp;&amp;&amp;</p>

    <div class="section-rule" style="top:341px"></div>
    <h2 class="section-title" style="left:87px;top:325px;width:266px">Sandwich Add Ons</h2>

    <p class="addon-name" style="left:21px;top:392px">Chips</p><p class="addon-price" style="left:108px;top:392px">$&amp;.&amp;&amp;</p>
    <p class="addon-name" style="left:21px;top:420px">Pretzels</p><p class="addon-price" style="left:108px;top:420px">$&amp;.&amp;&amp;</p>
    <p class="addon-name" style="left:21px;top:448px">Cookies</p><p class="addon-price" style="left:108px;top:448px">$&amp;.&amp;&amp;</p>
    <p class="addon-name" style="left:21px;top:477px">Brownie</p><p class="addon-price" style="left:108px;top:477px">$&amp;.&amp;&amp;</p>
    <p class="addon-name" style="left:21px;top:508px">Blondie</p><p class="addon-price" style="left:108px;top:508px">$&amp;.&amp;&amp;</p>
    <p class="addon-name" style="left:21px;top:540px">Whole Fruit</p><p class="addon-price" style="left:108px;top:540px">$&amp;.&amp;&amp;</p>
    <p class="addon-name" style="left:21px;top:572px">Gourmet Pasta Vegetable<br>Salad</p><p class="addon-price" style="left:108px;top:592px">$&amp;.&amp;&amp;</p>
    <p class="addon-name" style="left:21px;top:616px">Fresh Fruit Cups</p><p class="addon-price" style="left:108px;top:633px">$&amp;.&amp;&amp;</p>

    <p class="addon-name" style="left:223px;top:390px">Redskin Potato Salad</p><p class="addon-price" style="left:350px;top:408px">$&amp;.&amp;&amp;</p>
    <p class="addon-name" style="left:223px;top:435px">Sesame Noodle Salad</p><p class="addon-price" style="left:350px;top:452px">$&amp;.&amp;&amp;</p>
    <p class="addon-name" style="left:223px;top:483px">Couscous Salad</p><p class="addon-price" style="left:350px;top:483px">$&amp;.&amp;&amp;</p>
    <p class="addon-name" style="left:223px;top:519px">Caesar Salad</p><p class="addon-price" style="left:350px;top:519px">$&amp;.&amp;&amp;</p>
    <p class="addon-name" style="left:223px;top:554px">Tropical Salad</p><p class="addon-price" style="left:350px;top:554px">$&amp;.&amp;&amp;</p>
    <p class="addon-name" style="left:223px;top:589px">Farm Fresh Garden Salad</p><p class="addon-price" style="left:350px;top:607px">$&amp;.&amp;&amp;</p>
    <p class="addon-name" style="left:223px;top:630px">Country Cole Slaw</p><p class="addon-price" style="left:350px;top:630px">$&amp;.&amp;&amp;</p>

    <p class="notice" style="left:14px;width:396px">All Prices are per Person, with a 10 person minimum order per item chosen.<br>Local Products used when available and in season</p>

    <footer class="footer">
      <p class="footer__cta">CALL OR EMAIL US TODAY:</p>
      <p class="footer__phone">
        <svg width="24" height="20" viewBox="0 0 24 20" aria-hidden="true"><path d="M2 7 C2 2 22 2 22 7 L18 9 L16 6 L8 6 L6 9 Z M6 10 L18 10 L21 18 L3 18 Z" fill="var(--ink)"/><circle cx="12" cy="14" r="2.5" fill="var(--orange)"/></svg>
        410-555-0142
      </p>
      <p class="footer__address">218 Willow Bend Road<br>Dunkirk, MD 20754<br>www.harborfieldcaterers.com</p>
    </footer>

    <div class="brand">
      <span class="brand__dot"></span>
      <p class="brand__name">Harbor Field<br>Caterers</p>
    </div>
  </section>

  <!-- Page 8 -->
  <section class="page page--back">
    <svg class="photo" viewBox="0 0 568 744" role="img" aria-label="Photo of grilled chicken with herbs on a white plate">
      <defs>
        <linearGradient id="chickenTone" x1="0" y1="0" x2="1" y2="1">
          <stop offset="0" stop-color="var(--plate-light)"/>
          <stop offset=".45" stop-color="var(--chicken)"/>
          <stop offset=".8" stop-color="#8c6a3a"/>
          <stop offset="1" stop-color="var(--plate-light)"/>
        </linearGradient>
      </defs>
      <path d="M446 0 C420 170 500 340 428 517 L568 517 L568 0 Z" fill="url(#chickenTone)"/>
    </svg>

    <div class="section-rule" style="top:27px"></div>
    <h2 class="section-title" style="left:130px;top:12px;width:166px">Hot Entrees</h2>

    <h3 class="entree-name" style="top:71px">Chesapeake Crab Cake</h3>
    <p class="entree-desc" style="top:94px">6oz Jumbo Lump Crab Cake served with House-made Remoulade Oven Roasted Redskin Potatoes, and Sautéed Local Corn.</p>
    <p class="entree-price" style="top:114px">$&amp;.&amp;&amp;</p>

    <h3 class="entree-name" style="top:151px">Key West Grilled Salmon</h3>
    <p class="entree-desc" style="top:170px">served with Pina-Colada Jeweled Rice, Fire-Roasted Seasonal Vegetable Medley, and Fresh Mango Salsa.</p>
    <p class="entree-price" style="top:190px">$&amp;.&amp;&amp;</p>

    <h3 class="entree-name" style="top:226px">Tropical Grilled Chicken</h3>
    <p class="entree-desc" style="top:244px">Jamaican Jerk Rubbed Chicken Breast grilled and topped with Fresh Mango Salsa, served with Roasted Seasonal Vegetable Medley, Jeweled Jasmine Rice, Pineapple Hawaiian Cole Slaw.</p>
    <p class="entree-price" style="top:281px">$&amp;.&amp;&amp;</p>

    <h3 class="entree-name" style="top:314px;line-height:17px">Add Cilantro Grilled Mahi-Mahi and Fresh Mango<br>Salsa</h3>
    <p class="entree-price" style="top:331px">$&amp;.&amp;&amp;</p>

    <h3 class="entree-name" style="top:361px">Fried Chicken Picnic</h3>
    <p class="entree-desc" style="top:380px">Country Fried 8-cut Chicken served with Potato Salad, Pasta-Vegetable Salad, Creamy Cole Slaw, and Fresh Watermelon Wedge.</p>
    <p class="entree-price" style="top:400px">$&amp;.&amp;&amp;</p>

    <h3 class="entree-name" style="top:431px">Chicken Parmesan</h3>
    <p class="entree-desc" style="top:449px">Lightly Breaded Chicken Breast, golden fried, and topped with Chef-crafted Marinara, Melted Provolone and Mozzarella, and served with Penne Pasta.</p>
    <p class="entree-price" style="top:484px">$&amp;.&amp;&amp;</p>

    <h3 class="entree-name" style="top:506px">Fajita Lunch</h3>
    <p class="entree-desc" style="top:525px;width:400px">Your choice of grilled Chicken breast strips or grilled Sirloin Steak strips, Fire-Roasted Peppers and Onions, Flour Tortillas, Cuban Stewed Black Beans, Spanish Rice, and Fire-Roasted Seasonal Vegetable Medley.<br>Diced Tomatoes, Salsa, Sour Cream, Crisp Lettuce, Shredded Cheese, and Jalapeño Garni.</p>
    <p class="entree-price" style="top:600px">$&amp;.&amp;&amp;</p>

    <h3 class="entree-name" style="top:630px">Make it a Chicken and Beef Combo</h3>
    <p class="entree-price" style="top:628px">$&amp;.&amp;&amp;</p>

    <p class="notice" style="left:14px;width:396px">All Prices are per Person, with a 10 person minimum order per item chosen.<br>Local Products used when available and in season</p>

    <footer class="footer">
      <p class="footer__cta">CALL OR EMAIL US TODAY:</p>
      <p class="footer__phone">
        <svg width="24" height="20" viewBox="0 0 24 20" aria-hidden="true"><path d="M2 7 C2 2 22 2 22 7 L18 9 L16 6 L8 6 L6 9 Z M6 10 L18 10 L21 18 L3 18 Z" fill="var(--ink)"/><circle cx="12" cy="14" r="2.5" fill="var(--orange)"/></svg>
        410-555-0142
      </p>
      <p class="footer__address">218 Willow Bend Road<br>Dunkirk, MD 20754<br>www.harborfieldcaterers.com</p>
    </footer>

    <div class="brand">
      <span class="brand__dot"></span>
      <p class="brand__name">Harbor Field<br>Caterers</p>
    </div>
  </section>

</main>
</body>
</html>
```